Stationery for Villa Marenta Design Hotel**

Who we are:

Wander on an isolated beach while breathing in the fresh, salty, sea air. Listen to the warm Pacific wind rustling through green palm trees as you walk to a pristine lagoon. Feel the delicious warmth of the sun kiss your skin; the beach is yours. At Villa Marenta you can experience a vacation in undisturbed, natural beauty. We have created a place for you to find new strength, relaxation, and inner harmony. We offer total rest to the experienced traveler from all over the world.

We are a brand new and smartly built design-hotel (under construction) close to a unique beach and a fantastic surf spot in Huatulco, Southwest Mexico.

As you can see in the attachments, we do have an established corporate design, but as for now still need a format for booklets for information around our hotel and things to do in the area, important numbers (we fill in the content for that one).

Our corporate colors:
green #64b445, brown #b07043, blue #0ab7cf, yellow # f9b02a and #fcc01a, navy #444f69
Corporate fonts:
Krub and Miller Banner.
For further information access:
www.villamarenta.example
https://slidevault.example/view/QmPxLwZrTyKsNbVcHdJe/

Social Media: VillaMarenta

Industry/Entity Type

Hotel

Font styles to use
Other font styles liked:
• Krub, Miller Banner

Requirements
Must have
• Stick to Logo Design, defined corporate elements, logo, colors, fonts and general touch and feel
Nice to have
• Who we are:

Our corporate colors:
Corporate fonts:
Krub and Miller Banner.
www.villamarenta.example

Social Media: VillaMarenta

```html
<!DOCTYPE html>
<html lang="en">
<head>
<meta charset="utf-8">
<title>Villa Marenta Design Hotel – Stationery</title>
<link rel="stylesheet" href="https://fonts.googleapis.com/css2?family=Krub:wght@500&family=Libre+Baskerville&display=swap">
<style>
  :root {
    --bg: #a9abb8;
    --paper: #ffffff;
    --paper-shade: #ededee;
    --green: #64b445;
    --green-light: #8dcc63;
    --brown: #b07043;
    --blue: #0ab7cf;
    --teal: #1b9fab;
    --yellow: #f9b02a;
    --gold: #e0a52b;
    --leaf-tint: #dbe8cf;
  }
  * { box-sizing: border-box; margin: 0; padding: 0; }
  html, body { width: 1200px; height: 950px; overflow: hidden; }
  body { background: var(--bg); position: relative; font-family: "Krub", sans-serif; }

  .envelope-front {
    position: absolute; left: 150px; top: 45px;
    width: 900px; height: 405px;
    background: var(--paper);
    box-shadow: 0 6px 18px rgba(0,0,0,.18);
    overflow: hidden;
  }
  .leaf-decoration {
    position: absolute; right: 30px; top: -40px;
    width: 270px; height: 270px; border-radius: 50% 50% 45% 55%;
    background: radial-gradient(circle at 45% 45%, var(--leaf-tint), rgba(219,232,207,.55) 70%, rgba(255,255,255,0) 72%);
  }
  .sender {
    position: absolute; left: 45px; top: 210px;
  }
  .sender-mark { display: flex; align-items: center; gap: 10px; }
  .sender-square { width: 22px; height: 22px; border: 2px solid var(--gold); }
  .sender-name {
    font-family: "Krub", sans-serif; font-weight: 500;
    font-size: 22px; letter-spacing: 2px; text-transform: uppercase; color: var(--gold);
  }
  .sender-tagline {
    margin-top: 4px; font-size: 8px; letter-spacing: 2px; text-transform: uppercase; color: var(--gold);
  }
  .sender-address {
    margin-top: 6px; font-family: "Libre Baskerville", serif;
    font-size: 14px; line-height: 1.3; color: var(--green);
  }
  .edge-band { position: absolute; bottom: 0; height: 9px; }
  .edge-band--yellow { left: 0; width: 240px; background: var(--yellow); }
  .edge-band--green { left: 246px; width: 310px; background: var(--green-light); }
  .edge-band--blue { left: 562px; right: 0; background: var(--teal); }

  .envelope-back { position: absolute; left: 150px; top: 495px; width: 900px; height: 420px; }
</style>
</head>
<body>

<section class="envelope-front" aria-label="Envelope front">
  <div class="leaf-decoration" role="img" aria-label="Faint watercolour monstera leaf decoration"></div>
  <div class="sender">
    <div class="sender-mark">
      <span class="sender-square"></span>
      <span class="sender-name">Villa Marenta</span>
    </div>
    <p class="sender-tagline">design hotel · surf · beach</p>
    <p class="sender-address">Playa Serena, Costa Linda,<br>Mexiko</p>
  </div>
  <span class="edge-band edge-band--yellow"></span>
  <span class="edge-band edge-band--green"></span>
  <span class="edge-band edge-band--blue"></span>
</section>

<svg class="envelope-back" viewBox="0 0 900 420" aria-label="Envelope back with open flap">
  <rect class="envelope-body" x="0" y="55" width="900" height="365" fill="var(--paper)"/>
  <path class="envelope-flap" role="img" aria-label="Green patterned flap lining"
        d="M0 60 Q0 0 40 0 L860 0 Q900 0 900 40 L900 55 Q860 60 820 110 L120 110 Q60 75 0 85 Z"
        fill="var(--green-light)"/>
  <path class="envelope-pocket" d="M0 110 L840 110 Q870 112 900 150" fill="none" stroke="var(--paper-shade)" stroke-width="2"/>
  <path class="envelope-fold" d="M20 420 L20 150 Q20 120 50 115" fill="none" stroke="var(--paper-shade)" stroke-width="2"/>
</svg>

</body>
</html>
```